Property management company looking for modern card design

We at Blue Heron Partners provides property management services for its residential and commercial properties, with expertise in all categories of multifamily, industrial and office projects throughout California.

We need a business card design that is professional and modern designed business card. In our field, clients get hundreds of business cards, we would like our card to stand out.

Please avoid small print.

Target Market(s)

Professionals and high end clients

Industry/Entity Type

Financial Planning

Contact Information for Business Card

Company Name: Blue Heron Partners, Name, email, license #, phone number, website blueheronpartners.com

Font styles to use
Sans Serif

Requirements
Must have
• The card design needs to be adaptable because there is a possibly we will be expanding into different sectors other than real estate. The card design should be focused on financial planning and asset management.
Nice to have
• Modern and simple business card. Eye catching. Non-standard size/shaped cards would be great.
• blueheronpartners.com
Should not have
• Too many bright color or any pictures or shapes of real estate stuff.

```html
<!DOCTYPE html>
<html lang="en">
<head>
<meta charset="utf-8">
<title>Blue Heron Partners – Business Card</title>
<link href="https://fonts.googleapis.com/css2?family=Libre+Baskerville:wght@400&family=Open+Sans:wght@400;700&display=swap" rel="stylesheet">
<style>
  :root {
    --backdrop: #d8d5d0;
    --card-light: #e9e7e3;
    --card-dark: #2b2929;
    --accent-red: #e11f1f;
    --ink: #2a2a2a;
    --ink-soft: #4a4a4a;
    --white: #f4f4f4;
  }
  html, body {
    margin: 0;
    padding: 0;
    width: 1200px;
    height: 848px;
    overflow: hidden;
    background: var(--backdrop);
  }
  .canvas {
    position: relative;
    width: 1200px;
    height: 848px;
  }
  .card {
    position: absolute;
    top: 281px;
    width: 500px;
    height: 286px;
    border-radius: 22px;
    box-shadow: 0 10px 28px rgba(0,0,0,0.22);
    overflow: hidden;
  }
  .card--front { left: 70px; background: var(--card-light); }
  .card--back  { left: 630px; background: var(--card-dark); }

  .brand {
    display: flex;
    align-items: center;
    gap: 10px;
    font-family: "Open Sans", sans-serif;
    font-weight: 700;
    color: var(--accent-red);
    white-space: nowrap;
  }
  .brand__dot {
    border-radius: 50%;
    background: var(--accent-red);
    flex: none;
  }
  .card--front .brand {
    position: absolute;
    top: 28px;
    right: 30px;
    font-size: 17px;
  }
  .card--front .brand__dot { width: 22px; height: 22px; }

  .identity {
    position: absolute;
    left: 40px;
    top: 120px;
    padding-left: 16px;
    border-left: 7px solid var(--accent-red);
  }
  .identity__name {
    margin: 0;
    font-family: "Libre Baskerville", serif;
    font-size: 26px;
    line-height: 1.1;
    color: var(--ink);
  }
  .identity__title {
    margin: 2px 0 0;
    font-family: "Libre Baskerville", serif;
    font-size: 15px;
    color: var(--accent-red);
  }
  .contacts {
    position: absolute;
    left: 46px;
    top: 196px;
    margin: 0;
    padding: 0;
    list-style: none;
    font-family: "Open Sans", sans-serif;
    font-size: 15px;
    color: var(--ink-soft);
  }
  .contacts__item {
    display: flex;
    align-items: center;
    gap: 12px;
    height: 24px;
  }
  .contacts__icon { width: 16px; height: 16px; flex: none; }

  .card--back .brand {
    position: absolute;
    left: 50%;
    top: 50%;
    transform: translate(-50%, -50%);
    font-size: 32px;
    gap: 16px;
  }
  .card--back .brand__dot { width: 40px; height: 40px; }
</style>
</head>
<body>
<main class="canvas">
  <section class="card card--front" aria-label="Business card front">
    <div class="brand">
      <span class="brand__dot"></span>
      <span class="brand__name">Blue Heron Partners</span>
    </div>
    <div class="identity">
      <h1 class="identity__name">Your Name</h1>
      <p class="identity__title">Job Title</p>
    </div>
    <ul class="contacts">
      <li class="contacts__item">
        <svg class="contacts__icon" viewBox="0 0 16 16" aria-hidden="true"><path fill="#e11f1f" d="M1 5c0-2 3-3 7-3s7 1 7 3v1h-4V5H5v1H1zM4 7h8l2 7H2z"/></svg>
        <span>000 000 0000</span>
      </li>
      <li class="contacts__item">
        <svg class="contacts__icon" viewBox="0 0 16 16" aria-hidden="true"><rect x="1" y="3" width="14" height="10" fill="#e11f1f"/><path d="M1 3l7 6 7-6" fill="none" stroke="#e9e7e3" stroke-width="1.3"/></svg>
        <span>youremail@xyz.com</span>
      </li>
      <li class="contacts__item">
        <svg class="contacts__icon" viewBox="0 0 16 16" aria-hidden="true"><g fill="none" stroke="#e11f1f" stroke-width="1.2"><circle cx="8" cy="8" r="6.5"/><ellipse cx="8" cy="8" rx="3" ry="6.5"/><path d="M1.5 8h13M2.5 5h11M2.5 11h11"/></g></svg>
        <span>www.yourwebsite.com</span>
      </li>
    </ul>
  </section>

  <section class="card card--back" aria-label="Business card back">
    <div class="brand">
      <span class="brand__dot"></span>
      <span class="brand__name">Blue Heron Partners</span>
    </div>
  </section>
</main>
</body>
</html>
```